Design website home page for pathology consulting company

Starting a new consulting company with anatomic pathologists focused on expert diagnosis and second opinions on difficult pathology cases. In the near future we will be incorporating next generation diagnostics for rare diseases of childhood into the business. These include discovery and testing of DNA for mutations.

The company is formed around one of the best known pathologists in the world named Marcel "Biscuit" Trowell. The name of the company is "BiscuitLab"

We had a logo design by SketchForum - it is great. I will attach file as soon as I have it (contest ending today). Our company is medical, uses microscopes, DNA, probably will focus on childhood diseases but not solely on childhood diseases. we're not particularly conservative, but the customers we want to appeal to include older practicing pathologists as well as patients (sometimes parents) looking for second opinions.

Think a group of expert doctors diagnosing disease through the microscope and through DNA technology, ages ranging from 35-75 all trained by the best pathologist in the world - "Biscuit"

We receive glass slides from diseases from patients all over the world from docs who need an expert to tell them what is the diagnosis. So "path to the diagnosis" is also part of the company marketing message.

We want the website design to describe our company but be very simple to find what one is looking for as we will use it as the launch page to:
1) order services
2) check results/reports
3) set up new account
4) speak with one of the pathologists
5) see our test menu
6) access our educational material/webinars
Updates

Update - looking for home page design and then finalists will ask for second page design to keep with theme - ok?

Reason: realized this project isn't web design but web home page design - thanks

Reason: Holidays for some in next two weeks

Reason: Hot discussion among collaborators for a few of the submissions. Will provide detail individually this weekend. Thanks so much for all the submissions!

Target Market(s)

Referring pathologists, physicians who want second opinions on pathology disease diagnosis, patients who have had biopsies (either patients themselves or parents of patients), generally high education level

Industry/Entity Type

Marketing

Requirements
Must have
• BiscuitLab
Next Generation Pathology Consultants

```html
<!DOCTYPE html>
<html lang="en">
<head>
<meta charset="utf-8">
<title>BiscuitLab – Next Generation Pathology Consultants</title>
<link href="https://fonts.googleapis.com/css2?family=Open+Sans:wght@300;400;600&display=swap" rel="stylesheet">
<style>
  :root{
    --blue:#0a5ea8;
    --blue-text:#1468b0;
    --navy:#0c3e6c;
    --black:#000;
    --ink:#333;
    --muted:#666;
    --band:#efefef;
    --disc:#b1b1b1;
    --rule:#d8d8d8;
    --white:#fff;
  }
  *{box-sizing:border-box;margin:0;padding:0}
  html,body{width:983px;height:1200px;overflow:hidden;background:var(--white)}
  body{position:relative;font-family:"Open Sans",Arial,sans-serif;color:var(--ink)}
  .abs{position:absolute}

  /* navigation */
  .main-nav{position:absolute;left:0;top:0;width:983px;height:37px;background:var(--blue)}
  .main-nav a{position:absolute;top:0;line-height:37px;font-size:10.5px;color:var(--white);text-decoration:none;white-space:nowrap}
  .main-nav .current{left:81px;width:60px;background:var(--black);text-align:center;font-weight:600}

  /* header */
  .logo-badge{position:absolute;left:454px;top:4px;width:74px;height:74px;border-radius:50%;background:var(--white);border:2px solid #e3e3e3}
  .brand-name{position:absolute;left:391px;top:64px;width:200px;text-align:center;font-size:20px;font-weight:400;color:var(--blue);letter-spacing:.5px}
  .brand-tagline{position:absolute;left:391px;top:88px;width:200px;text-align:center;font-size:6.5px;color:var(--muted)}
  .social-rings{position:absolute;left:81px;top:61px;display:flex;gap:4px}
  .social-rings span{width:22px;height:22px;border-radius:50%;border:1.5px solid #d6d6d6}
  .btn-account,.btn-speak{position:absolute;top:59px;height:26px;line-height:26px;text-align:center;font-size:10.5px;color:var(--white)}
  .btn-account{left:613px;width:116px;background:var(--black)}
  .btn-speak{left:739px;width:162px;background:#c7c7c7}

  /* hero */
  .hero-photo{position:absolute;left:0;top:109px;width:983px;height:389px;
    background:linear-gradient(100deg,#c9c3c0 0%,#8f8a92 22%,#3c4470 45%,#2d3a8c 62%,#4a56b0 80%,#6f7ac0 100%)}
  .hero-copy{position:absolute;left:633px;top:211px;width:280px;color:var(--white)}
  .hero-copy h1{font-size:23px;font-weight:400;line-height:30px}
  .hero-copy h2{font-size:14px;font-weight:600;line-height:18px}
  .hero-copy p{margin-top:9px;font-size:10.2px;line-height:17.2px}
  .btn-discover{position:absolute;left:633px;top:347px;width:107px;height:29px;line-height:29px;text-align:center;
    font-size:10.5px;color:#333;font-weight:600;background:linear-gradient(#f6f6f6,#d8d8d8);border:1px solid #bbb}

  /* feature band */
  .feature-band{position:absolute;left:0;top:498px;width:983px;height:262px;background:var(--band)}
  .feature{position:absolute;top:529px;width:280px;text-align:center}
  .feature .disc{width:132px;height:132px;margin:0 auto;border-radius:50%;background:var(--disc);border:2px solid #c4c4c4;display:flex;align-items:center;justify-content:center}
  .feature h3{margin-top:10px;font-size:20.5px;font-weight:400;color:var(--blue-text);line-height:26px;white-space:nowrap}
  .feature .btn-click{display:inline-block;margin-top:9px;width:87px;height:22px;line-height:22px;font-size:12px;color:var(--white);background:var(--navy)}

  /* content */
  .section-title{font-size:19.5px;font-weight:400;color:#222;line-height:24px}
  .lead{font-size:11.5px;font-weight:300;line-height:17px;color:#555}
  .service-list{list-style:none}
  .service-list li{height:24.6px;font-size:8.8px;color:#444;display:flex;align-items:center;gap:15px;white-space:nowrap}
  .bullet{width:10px;height:10px;flex:none}
  .feature-photo{position:absolute;left:359px;top:799px;width:313px;height:114px;background:linear-gradient(90deg,#d9b9a4 0%,#e9e4e0 35%,#8fa3b8 65%,#3b7ec4 100%)}
  .story-title{font-size:19px;font-weight:400;line-height:23px;color:var(--blue-text);letter-spacing:-.3px}
  .new-services h4{font-size:14px;font-weight:400;color:var(--blue-text);line-height:18px}
  .new-services p{margin-top:10px;font-size:11.5px;font-weight:300;line-height:17px;color:#555}
  .new-services .item{position:absolute;left:0;width:197px;height:81px;border-bottom:1px solid var(--rule)}
  .btn-more{position:absolute;left:704px;top:1101px;width:81px;height:30px;line-height:30px;text-align:center;font-size:9px;background:#eee;color:#222}

  /* footer */
  .site-footer{position:absolute;left:0;top:1159px;width:983px;height:41px;background:var(--black)}
  .site-footer p{position:absolute;left:82px;top:0;line-height:41px;font-size:10px;color:var(--white)}
  .footer-social{position:absolute;left:823px;top:13px;display:flex;gap:8px}
  .footer-social span{width:15px;height:15px;border-radius:50%;background:var(--white)}
</style>
</head>
<body>

<nav class="main-nav">
  <a class="current" href="#">Home</a>
  <a style="left:170px" href="#">About Us</a>
  <a style="left:255px" href="#">Services</a>
  <a style="left:339px" href="#">Pathology Consultants</a>
  <a style="left:533px" href="#">Patients</a>
  <a style="left:638px" href="#">Results</a>
  <a style="left:741px" href="#">Accounts</a>
  <a style="left:849px" href="#">Contact Us</a>
</nav>

<header>
  <div class="logo-badge"></div>
  <div class="brand-name">BiscuitLab</div>
  <div class="brand-tagline">Next Generation Pathology Consultants</div>
  <div class="social-rings"><span></span><span></span><span></span><span></span></div>
  <a class="btn-account">Setup New Account</a>
  <a class="btn-speak">Speak With Pathologist</a>
</header>

<section>
  <div class="hero-photo" role="img" aria-label="Pathologist looking into a microscope in a blue-lit laboratory"></div>
  <div class="hero-copy">
    <h1>BiscuitLab</h1>
    <h2>Next Generation Pathology Consultants</h2>
    <p>Sed ut perspiciatis unde omnis iste natus error sit voluptatem accusantium doloremque laudantium, totam rem aperiam, eaque ipsa quae ab illo inventore veritatis et quasi architecto beatae vitae dicta sunt explicabo.</p>
  </div>
  <a class="btn-discover">Discover More</a>
</section>

<section class="feature-band"></section>
<div class="feature" style="left:56px">
  <div class="disc">
    <svg width="66" height="72" viewBox="0 0 66 72" fill="none" stroke="#fff" stroke-width="3">
      <ellipse cx="33" cy="36" rx="30" ry="11"/>
      <ellipse cx="33" cy="36" rx="30" ry="11" transform="rotate(60 33 36)"/>
      <ellipse cx="33" cy="36" rx="30" ry="11" transform="rotate(-60 33 36)"/>
      <circle cx="33" cy="36" r="4" fill="#fff"/>
    </svg>
  </div>
  <h3>OUR TEST MENU</h3>
  <a class="btn-click">Click Here</a>
</div>
<div class="feature" style="left:351px">
  <div class="disc">
    <svg width="60" height="72" viewBox="0 0 60 72" fill="#fff">
      <rect x="26" y="4" width="10" height="34" rx="2" transform="rotate(35 31 21)"/>
      <rect x="6" y="38" width="26" height="5" rx="2"/>
      <path d="M40 30 q14 14 6 32 h-10 q8-14-2-26z"/>
      <rect x="4" y="63" width="52" height="6" rx="2"/>
    </svg>
  </div>
  <h3>PATHOLOGY CONSULTANTS</h3>
  <a class="btn-click">Click Here</a>
</div>
<div class="feature" style="left:647px">
  <div class="disc">
    <svg width="84" height="64" viewBox="0 0 84 64">
      <path fill="#fff" d="M18 62 a16 16 0 0 1 0-32 a22 22 0 0 1 42-8 a18 18 0 0 1 8 40z"/>
      <rect x="32" y="24" width="20" height="30" rx="3" fill="none" stroke="#b1b1b1" stroke-width="3"/>
      <path d="M42 32v14M35 39h14" stroke="#b1b1b1" stroke-width="3"/>
    </svg>
  </div>
  <h3>CARE ADVICE</h3>
  <a class="btn-click">Click Here</a>
</div>

<section class="our-services">
  <h2 class="section-title abs" style="left:81px;top:794px">OUR SERVICES</h2>
  <p class="lead abs" style="left:80px;top:847px;width:245px">Sed ut perspiciatis unde omnis iste natus error sit voluptatem accusantium doloremque laudantium, totam rem aperiam.</p>
  <ul class="service-list abs" style="left:81px;top:908px">
    <li><svg class="bullet" viewBox="0 0 10 10"><rect width="10" height="10" fill="#0a5ea8"/><path d="M4 2.5l3 2.5-3 2.5" stroke="#fff" stroke-width="1.4" fill="none"/></svg><span style="text-decoration:underline">AUTOPSY PATHOLOGY</span></li>
    <li><svg class="bullet" viewBox="0 0 10 10"><rect width="10" height="10" fill="#0a5ea8"/><path d="M4 2.5l3 2.5-3 2.5" stroke="#fff" stroke-width="1.4" fill="none"/></svg>BONE AND SOFT TISSUE PATHOLOGY</li>
    <li><svg class="bullet" viewBox="0 0 10 10"><rect width="10" height="10" fill="#0a5ea8"/><path d="M4 2.5l3 2.5-3 2.5" stroke="#fff" stroke-width="1.4" fill="none"/></svg>CLINICALLY INTERACTIVE CONSULTATIVE</li>
    <li><svg class="bullet" viewBox="0 0 10 10"><rect width="10" height="10" fill="#0a5ea8"/><path d="M4 2.5l3 2.5-3 2.5" stroke="#fff" stroke-width="1.4" fill="none"/></svg>DERMATOPATHOLOGY</li>
    <li><svg class="bullet" viewBox="0 0 10 10"><rect width="10" height="10" fill="#0a5ea8"/><path d="M4 2.5l3 2.5-3 2.5" stroke="#fff" stroke-width="1.4" fill="none"/></svg>FORENSIC PATHOLOGY</li>
    <li><svg class="bullet" viewBox="0 0 10 10"><rect width="10" height="10" fill="#0a5ea8"/><path d="M4 2.5l3 2.5-3 2.5" stroke="#fff" stroke-width="1.4" fill="none"/></svg>GASTROINTESTINAL &amp; HEPATIC</li>
    <li><svg class="bullet" viewBox="0 0 10 10"><rect width="10" height="10" fill="#0a5ea8"/><path d="M4 2.5l3 2.5-3 2.5" stroke="#fff" stroke-width="1.4" fill="none"/></svg>HEMATOLOGY &amp; HEMATO</li>
    <li><svg class="bullet" viewBox="0 0 10 10"><rect width="10" height="10" fill="#0a5ea8"/><path d="M4 2.5l3 2.5-3 2.5" stroke="#fff" stroke-width="1.4" fill="none"/></svg>IMMUNOPATHOLOGY/HISTOPATHOLOGY</li>
    <li><svg class="bullet" viewBox="0 0 10 10"><rect width="10" height="10" fill="#0a5ea8"/><path d="M4 2.5l3 2.5-3 2.5" stroke="#fff" stroke-width="1.4" fill="none"/></svg>PEDIATRIC PATHOLOGY</li>
  </ul>
</section>

<article class="story">
  <div class="feature-photo" role="img" aria-label="Smiling lab technician at a workbench with laboratory equipment"></div>
  <h2 class="story-title abs" style="left:359px;top:927px;width:330px">SED UT PERSPICIATIS UNDE OMNIS<br>ISTE NATUS ERROR SIT VOLTATEM<br>ACCNTIM DOLOREMQUE</h2>
  <p class="lead abs" style="left:359px;top:1006px;width:315px">Sed ut perspiciatis unde omnis iste natus error sit voluptatem accusantium doloremque laudantium, totam rem aperiam, eaque ipsa quae ab illo inventore veritatis et quasi architecto beatae vitae dicta sunt explicabo.</p>
  <p class="lead abs" style="left:359px;top:1092px;width:315px">Nemo enim ipsam voluptatem quia voluptas sit aspernatur aut odit aut fugit, sed quia consequuntur.</p>
</article>

<aside class="new-services">
  <h2 class="section-title abs" style="left:704px;top:794px">NEW SERVICES</h2>
  <div class="abs" style="left:703px;top:848px;width:198px;height:240px">
    <div class="item" style="top:0"><h4>1. Cosmetic Surgery</h4><p>Sed ut perspiciatis unde omnis iste natus error sit voluptatem</p></div>
    <div class="item" style="top:81px"><h4>2. Minor Oral Surgery</h4><p>Sed ut perspiciatis unde omnis iste natus error sit voluptatem</p></div>
    <div class="item" style="top:162px"><h4>3. Restorative Services</h4><p>Sed ut perspiciatis unde omnis iste natus error sit voluptatem</p></div>
  </div>
  <a class="btn-more">READ MORE</a>
</aside>

<footer class="site-footer">
  <p>Copyright © 2013 Consultants, Inc . All Rights Reserved</p>
  <div class="footer-social"><span></span><span></span><span></span><span></span></div>
</footer>

</body>
</html>
```